ro dun magazine

just need coupons of real customers made for my magazine, I have the layout or temp lets of the magazine i just need the coupons to be made and plug-in. i have examples, of the ads or coupons, I'm sure they will need to redone. and in a section of the magazine their in a church directory. with this section , i need the pic of the pastor plug in with their church information and in do have some ex-samples of that as well. with the websites of the businesses. if you need to grab an image from their site . you'll be able to do so. all of the business are in the upload section , these are small base business so a lot of the ads and logos need redone any way . so i will look at it and let you know.

P.S with the new coupons and logos I'm trying to impress these customers to stay with the magazine

Target Market(s)

small businesses

Requirements
Must have
• good graphics
Should not have
• not pixelated graphics

```html
<!DOCTYPE html>
<html lang="en">
<head>
<meta charset="utf-8">
<title>RO &amp; DUN Pastry Kitchen Bakery – Business Card</title>
<link rel="stylesheet" href="https://fonts.googleapis.com/css2?family=Marcellus&family=Arimo:wght@400&display=swap">
<style>
  :root {
    --backdrop: #808080;
    --card: #ffffff;
    --brand-ink: #1e0a04;
    --tagline: #a0286a;
    --contact-ink: #111111;
    --petal-red: #ff0000;
    --petal-dark: #5e0004;
  }
  * { margin: 0; padding: 0; box-sizing: border-box; }
  html, body {
    width: 1200px;
    height: 1200px;
    overflow: hidden;
    background: var(--backdrop);
  }
  .business-card {
    position: absolute;
    left: 68px;
    top: 320px;
    width: 1064px;
    height: 559px;
    background: var(--card);
    overflow: hidden;
  }
  .brand-name {
    position: absolute;
    left: 67px;
    top: 83px;
    width: 755px;
    font-family: "Marcellus", serif;
    font-weight: 400;
    font-size: 162px;
    line-height: 1;
    color: var(--brand-ink);
    white-space: nowrap;
    letter-spacing: -2px;
    word-spacing: -14px;
  }
  .tagline {
    position: absolute;
    left: 235px;
    top: 246px;
    font-family: "Arimo", Arial, sans-serif;
    font-size: 54px;
    line-height: 1;
    color: var(--tagline);
    white-space: nowrap;
  }
  .contact {
    position: absolute;
    left: 0;
    width: 100%;
    font-family: "Arimo", Arial, sans-serif;
    font-size: 31px;
    line-height: 1;
    color: var(--contact-ink);
    white-space: nowrap;
  }
  .contact-online { top: 385px; padding-left: 92px; }
  .contact-address {
    top: 432px;
    padding-left: 193px;
    display: flex;
    align-items: center;
    gap: 14px;
  }
  .pin-icon { width: 28px; height: 36px; flex: none; }
  .corner-flourish {
    position: absolute;
    left: 840px;
    top: 16px;
    width: 208px;
    height: 364px;
  }
</style>
</head>
<body>
  <section class="business-card">
    <h1 class="brand-name">RO &amp; DUN</h1>
    <p class="tagline">Pastry Kitchen Bakery</p>

    <p class="contact contact-online">www.rodunbakes.com I hello@rodunbakes.com I 555.014.200</p>
    <p class="contact contact-address">
      <svg class="pin-icon" viewBox="0 0 28 36" aria-hidden="true">
        <path d="M14 0C6.3 0 0 6.1 0 13.6 0 23.2 14 36 14 36s14-12.8 14-22.4C28 6.1 21.7 0 14 0z" fill="var(--contact-ink)"/>
        <circle cx="14" cy="13.5" r="5" fill="var(--card)"/>
      </svg>
      <span>48 Maple Ave. Fairview, PA 15000</span>
    </p>

    <svg class="corner-flourish" viewBox="0 0 208 364" role="img" aria-label="Decorative red flower petals fanning from the card's right edge">
      <defs>
        <linearGradient id="petal-tone" x1="0" y1="0" x2="1" y2="1">
          <stop offset="0" stop-color="var(--petal-red)"/>
          <stop offset="0.6" stop-color="var(--petal-red)"/>
          <stop offset="1" stop-color="var(--petal-dark)"/>
        </linearGradient>
      </defs>
      <rect width="208" height="364" fill="url(#petal-tone)"/>
    </svg>
  </section>
</body>
</html>
```